Velk Partners Building Business Cards

We need a business card that reflects our business as "Solar Experts" in San Diego. Browse our website www.velkpartners.example our License needs to be displayed as "CSLB# 3867140" our phone number is (619) 555-0187

Save thousands on your electric bills and increase the value of your home while helping to protect the environment. Our solar installation experts will help you design the system that's right for you, using only the highest quality equipment that will look great and give you ideal performance. Our goal is to make you energy independent, and get your electric bill to 0.

Paul Osterby
(619) 555-0187
paul@velkpartners.example

Target Market(s)

Home owners in san diego looking for solar

Industry/Entity Type

Solar Energy

Contact Information for Business Card

Paul Osterby
(619) 555-0187
paul@velkpartners.example

Font styles to use
Other font styles liked:
• Use our logo font

Requirements
Must have
• License needs to be displayed as "CSLB# 3867140" our phone number is (619) 555-0187
Nice to have
• Real images of rooftop home solar in san diego
Should not have
• our business address

```html
<!DOCTYPE html>
<html lang="en">
<head>
<meta charset="utf-8">
<title>Velk Partners Building – Business Card</title>
<link rel="stylesheet" href="https://fonts.googleapis.com/css2?family=Roboto:wght@400;500;700&display=swap">
<style>
  :root {
    --navy: #1f3a66;
    --orange: #e3a020;
    --card-top: #f4f3f1;
    --card-bottom: #e6e4e1;
    --page: #d9d2c8;
    --band-text: #d7dce4;
    --body-text: #2a3550;
  }
  * { margin: 0; padding: 0; box-sizing: border-box; }
  html, body {
    width: 1200px; height: 1200px; overflow: hidden;
    background: var(--page);
    font-family: "Roboto", Arial, sans-serif;
  }
  .card {
    position: absolute; left: 75px; top: 289px;
    width: 1050px; height: 622px;
    background: linear-gradient(160deg, var(--card-top), var(--card-bottom));
    border: 1px solid rgba(255,255,255,0.7);
    box-shadow: 0 8px 30px rgba(0,0,0,0.12);
    overflow: hidden;
  }
  .accent-bar {
    position: absolute; left: 0; top: 52px;
    width: 28px; height: 102px;
    background: var(--orange);
  }
  .person { position: absolute; left: 59px; top: 64px; }
  .person-name {
    font-size: 33px; font-weight: 700; color: var(--navy);
    line-height: 1.1;
  }
  .person-title {
    margin-top: 8px;
    font-size: 23px; font-weight: 400; color: var(--navy);
  }
  .company-name {
    position: absolute; right: 43px; top: 66px;
    font-size: 44px; font-weight: 700; color: var(--navy);
    white-space: nowrap;
  }
  .contact-list {
    position: absolute; left: 64px; top: 458px;
    list-style: none;
  }
  .contact-item {
    display: flex; align-items: center;
    height: 37px;
    font-size: 24px; color: var(--body-text);
  }
  .contact-icon { width: 26px; height: 22px; margin-right: 22px; flex: none; }
  .contact-icon svg { width: 26px; height: 22px; display: block; }
  .web-domain { color: var(--orange); }
  .license-band {
    position: absolute; left: 628px; top: 500px;
    width: 422px; height: 59px;
  }
  .license-band svg { position: absolute; inset: 0; }
  .license-text {
    position: absolute; left: 58px; top: 0; line-height: 59px;
    font-size: 25px; color: var(--band-text); white-space: nowrap;
  }
</style>
</head>
<body>
  <div class="card">
    <div class="accent-bar"></div>

    <div class="person">
      <div class="person-name">Paul Osterby</div>
      <div class="person-title">Managing Director</div>
    </div>

    <div class="company-name">Velk Partners Building</div>

    <ul class="contact-list">
      <li class="contact-item">
        <span class="contact-icon">
          <svg viewBox="0 0 26 22" aria-hidden="true">
            <path d="M3 7 Q13 1 23 7 L21 10 L17 8.5 L17 6.5 Q13 5 9 6.5 L9 8.5 L5 10 Z" fill="var(--orange)"/>
            <rect x="6" y="11" width="14" height="9" rx="1.5" fill="var(--orange)"/>
          </svg>
        </span>
        (619) 555-0187
      </li>
      <li class="contact-item">
        <span class="contact-icon">
          <svg viewBox="0 0 26 22" aria-hidden="true" fill="none" stroke="var(--orange)" stroke-width="1.8">
            <circle cx="13" cy="11" r="9"/>
            <ellipse cx="13" cy="11" rx="4" ry="9"/>
            <line x1="4" y1="11" x2="22" y2="11"/>
          </svg>
        </span>
        paul@velkpartners.example
      </li>
      <li class="contact-item">
        <span class="contact-icon">
          <svg viewBox="0 0 26 22" aria-hidden="true">
            <rect x="3" y="4" width="20" height="14" fill="var(--orange)"/>
            <path d="M3 4 L13 12 L23 4" fill="none" stroke="#f2efe9" stroke-width="1.6"/>
          </svg>
        </span>
        <span>www.<span class="web-domain">velkpartners</span>.example</span>
      </li>
    </ul>

    <div class="license-band">
      <svg viewBox="0 0 422 59" preserveAspectRatio="none" aria-hidden="true">
        <polygon points="22,0 422,0 422,59 0,59" fill="var(--navy)"/>
      </svg>
      <span class="license-text">License: CSLB# 3867140</span>
    </div>
  </div>
</body>
</html>
```